Vortaleen - Lead the Way!

Vortaleen is a new Silicon Valley company, of the pimrela founders from Berlin, which provides a "Shared Hive Circle". This platform allows the crowd to support startups with money, experts and fame. Our Vision is, that everyone should become an entrepreneur.

Pls find all brief details in the attached document
Updates

Would be nice to have a list of more social services I'm available on, like a list of pictograms of all my services:

Find me on: chattro, fennwix+, qrt, mivrel, datebloom, pohk, rplex, etc...

pls make sure to use the right font:
http://www.typelarder-demo.com/fonts/Orbitron

Target Market(s)

Main target market is those already involved in the startup industry, by fundraising, investing, advising, cofounding and working. Vortaleen brings a totaly new transparency and collaborative way of starting companies to that business.

· Entrepreneurs (looking for funding, team and community)
· Investors (looking for hot investments and )
· Experts (workers looking for startups they can work for equity)
· Incubators & Business Schools (looking for tools to advise startups)

Industry/Entity Type

It Company

Requirements
Must have
• Pls find all brief details in the attached document
Nice to have

```html
<!DOCTYPE html>
<html lang="en">
<head>
<meta charset="utf-8">
<title>Vortaleen Business Card</title>
<link href="https://fonts.googleapis.com/css2?family=Orbitron:wght@400;500;700&family=Arimo:wght@400;700&display=swap" rel="stylesheet">
<style>
  :root {
    --backdrop: #e9e7e4;
    --night: #0a0f24;
    --navy: #1b2a66;
    --navy-deep: #101a45;
    --ufo-orange: #ee6a3d;
    --paper: #f7f6f8;
    --ink: #1d1d22;
    --muted: #4b4e57;
    --social-blue: #3a6fb4;
    --rule: #9c9ca4;
  }
  * { box-sizing: border-box; margin: 0; padding: 0; }
  html, body {
    width: 1200px; height: 900px; overflow: hidden;
    background: var(--backdrop);
  }
  .canvas { position: relative; width: 1200px; height: 900px; }
  .card {
    position: absolute; top: 295px; width: 540px; height: 310px;
    border-radius: 18px; overflow: hidden; background: var(--paper);
    box-shadow: 0 6px 18px rgba(0,0,0,0.25);
  }
  .card-front { left: 30px; }
  .card-back { left: 630px; }

  /* front */
  .front-sky {
    position: absolute; inset: 0 0 auto 0; height: 170px;
    background: radial-gradient(ellipse at 48% 45%, #2d4593 0%, var(--navy) 40%, var(--night) 100%);
  }
  .brand-mark {
    position: absolute; left: 178px; top: 30px; width: 120px; height: 120px;
    text-align: center;
  }
  .brand-dot {
    display: block; width: 44px; height: 44px; margin: 0 auto;
    border-radius: 50%; background: var(--ufo-orange);
  }
  .brand-name {
    display: block; margin-top: 14px;
    font: 700 28px Arimo, Arial, sans-serif; color: #fff; letter-spacing: 0.5px;
    white-space: nowrap; margin-left: -20px; margin-right: -20px;
  }
  .brand-tagline {
    position: absolute; left: 270px; top: 140px;
    font: 700 12px Arimo, Arial, sans-serif; color: #fff;
  }
  .front-info {
    position: absolute; top: 170px; left: 0; right: 0; height: 110px;
  }
  .person { position: absolute; left: 46px; top: 32px; text-align: center; }
  .person-name { font: 700 20px Arimo, Arial, sans-serif; color: var(--ink); }
  .person-role { font: 400 16px Arimo, Arial, sans-serif; color: var(--ink); margin-top: 4px; }
  .divider {
    position: absolute; left: 264px; top: 14px; width: 2px; height: 82px;
    background: var(--rule);
  }
  .contacts { position: absolute; left: 300px; top: 10px; list-style: none; }
  .contacts li {
    display: flex; align-items: center; gap: 9px; height: 18px;
    font: 400 13px Arimo, Arial, sans-serif; color: var(--ink);
  }
  .contacts svg { width: 11px; height: 11px; flex: none; }
  .social-square { width: 11px; height: 11px; border-radius: 2px; background: var(--social-blue); flex: none; }
  .front-footer {
    position: absolute; bottom: 0; left: 0; right: 0; height: 30px;
    background: linear-gradient(90deg, var(--night), #1c2350 50%, var(--night));
  }

  /* back */
  .back-sky {
    position: absolute; inset: 0 0 auto 0; height: 175px;
    background: linear-gradient(90deg, var(--night) 0%, var(--navy-deep) 45%, var(--navy) 100%);
  }
  .moon {
    position: absolute; right: -50px; top: -40px; width: 190px; height: 190px;
    border-radius: 50%;
    background: radial-gradient(circle at 40% 40%, #d4d4d4 0%, #9d9d9d 55%, #6a6a70 100%);
  }
  .back-dot {
    position: absolute; left: 282px; top: 20px; width: 26px; height: 26px;
    border-radius: 50%; background: var(--ufo-orange);
  }
  .headline {
    position: absolute; left: 0; right: 0; top: 40px; text-align: center;
    font-family: Orbitron, sans-serif; font-weight: 500; color: #fff; line-height: 1;
  }
  .headline-top { display: block; font-size: 54px; }
  .headline-bottom { display: block; font-size: 46px; margin-top: 8px; }
  .back-info {
    position: absolute; top: 175px; left: 0; right: 0; bottom: 0;
    background: linear-gradient(160deg, var(--paper) 60%, #dcdce2 100%);
  }
  .questions {
    list-style: none; text-align: center; margin-top: 14px;
    font: 400 16px Orbitron, sans-serif; color: var(--ink); letter-spacing: 0.6px;
  }
  .questions li { height: 32px; padding-top: 4px; }
  .questions li.ruled span { border-bottom: 1px solid var(--muted); padding-bottom: 3px; }
  .join {
    display: flex; justify-content: center; align-items: center; gap: 8px;
    margin-top: 4px; font: 400 10px Arimo, Arial, sans-serif; color: var(--ink);
  }
  .join-network { font: 700 15px Arimo, Arial, sans-serif; color: var(--social-blue); }
</style>
</head>
<body>
<main class="canvas">

  <section class="card card-front" aria-label="Business card front">
    <div class="front-sky" role="img" aria-label="Deep blue night sky with soft light burst"></div>
    <div class="brand-mark">
      <span class="brand-dot"></span>
      <span class="brand-name">Vortaleen</span>
    </div>
    <p class="brand-tagline">Lead the Way!</p>
    <div class="front-info">
      <div class="person">
        <p class="person-name">Marek Dunholt</p>
        <p class="person-role">Founder and CEO</p>
      </div>
      <div class="divider"></div>
      <ul class="contacts">
        <li>
          <svg viewBox="0 0 12 12"><rect x="3" y="0.5" width="6" height="11" rx="1.2" fill="none" stroke="#1d1d22" stroke-width="1.2"/><rect x="4.3" y="2" width="3.4" height="5" fill="#1d1d22"/></svg>
          0400 3187
        </li>
        <li>
          <svg viewBox="0 0 12 12"><rect x="0.6" y="2.2" width="10.8" height="7.6" fill="none" stroke="#1d1d22" stroke-width="1.1"/><path d="M0.6 2.2 L6 6.6 L11.4 2.2" fill="none" stroke="#1d1d22" stroke-width="1.1"/></svg>
          marek@vortaleen.com
        </li>
        <li><span class="social-square"></span>/marekdunholt</li>
        <li><span class="social-square"></span>/marekdunholt</li>
        <li><span class="social-square"></span>/in/marekdunholt</li>
      </ul>
    </div>
    <div class="front-footer"></div>
  </section>

  <section class="card card-back" aria-label="Business card back">
    <div class="back-sky"></div>
    <div class="moon" role="img" aria-label="Grey moon rising at the top right"></div>
    <span class="back-dot"></span>
    <h1 class="headline">
      <span class="headline-top">Are you</span>
      <span class="headline-bottom">interested in?</span>
    </h1>
    <div class="back-info">
      <ul class="questions">
        <li class="ruled"><span>Starting your own Business?</span></li>
        <li class="ruled"><span>Investing in hot Startups?</span></li>
        <li><span>Working for the next “Kindora”?</span></li>
      </ul>
      <p class="join">Join us on <span class="join-network">Kindora</span> /Vortaleen</p>
    </div>
  </section>

</main>
</body>
</html>
```